Keystone Trench Co Business Card*

Looking for a professional, clean and crisp business card

I am in the underground utilities industry and am just looking for a really impressive business card. I would like our card to be white with our symbol crisp and clear with it protruding. I also have a business partner that will require his name and info on the card once the design is set. I would like to have our website info on the card which is;
http://keystonetrenchco.example/

Contact Information for Business Card

Website, contact name, number and email

```html
<!DOCTYPE html>
<html lang="en">
<head>
<meta charset="utf-8">
<title>Keystone Trench Co Business Card</title>
<link href="https://fonts.googleapis.com/css2?family=Lato:wght@400;700&display=swap" rel="stylesheet">
<style>
  :root {
    --page-bg: #e9e6e2;
    --card-light: #f6f5f3;
    --panel-dark-top: #34363a;
    --panel-dark-bottom: #0d0e10;
    --accent-blue: #3d5d94;
    --text-grey: #b9b4ac;
    --icon-grey: #7d8794;
    --brand-ink: #1b1c1e;
  }
  html, body {
    margin: 0;
    padding: 0;
    width: 1200px;
    height: 1047px;
    overflow: hidden;
    background: var(--page-bg);
    font-family: "Lato", sans-serif;
  }
  .business-card {
    position: absolute;
    left: 100px;
    top: 238px;
    width: 1000px;
    height: 572px;
    border-radius: 26px;
    overflow: hidden;
    background: var(--card-light);
    box-shadow: 0 18px 40px rgba(0,0,0,0.18);
  }
  .card-shape {
    position: absolute;
    inset: 0;
  }
  .contact-side {
    position: absolute;
    left: 42px;
    top: 0;
    color: var(--text-grey);
  }
  .person-name {
    position: absolute;
    top: 106px;
    margin: 0;
    font-size: 34px;
    font-weight: 700;
    color: var(--accent-blue);
    white-space: nowrap;
  }
  .person-role {
    position: absolute;
    top: 154px;
    margin: 0;
    font-size: 21px;
    white-space: nowrap;
  }
  .divider {
    position: absolute;
    top: 218px;
    width: 54px;
    height: 2px;
    background: var(--accent-blue);
  }
  .address {
    position: absolute;
    top: 256px;
    margin: 0;
    font-style: normal;
    font-size: 22px;
    line-height: 29px;
    white-space: nowrap;
  }
  .contact-list {
    position: absolute;
    top: 336px;
    margin: 0;
    padding: 0;
    list-style: none;
    font-size: 22px;
  }
  .contact-list li {
    display: flex;
    align-items: center;
    height: 32px;
    white-space: nowrap;
  }
  .contact-list svg {
    width: 20px;
    height: 20px;
    margin-right: 22px;
    flex: none;
  }
  .brand-mark {
    position: absolute;
    left: 737px;
    top: 286px;
    transform: translate(-50%, -50%);
    display: flex;
    align-items: center;
    gap: 14px;
    white-space: nowrap;
  }
  .brand-dot {
    width: 26px;
    height: 26px;
    border-radius: 50%;
    background: var(--accent-blue);
  }
  .brand-name {
    font-size: 30px;
    font-weight: 700;
    color: var(--brand-ink);
  }
</style>
</head>
<body>
  <div class="business-card">
    <svg class="card-shape" width="1000" height="572" viewBox="0 0 1000 572" aria-hidden="true">
      <defs>
        <linearGradient id="panelGradient" x1="0" y1="0" x2="0.6" y2="1">
          <stop offset="0" stop-color="var(--panel-dark-top)"/>
          <stop offset="1" stop-color="var(--panel-dark-bottom)"/>
        </linearGradient>
      </defs>
      <path class="dark-panel" d="M0,0 H548 C470,120 450,420 520,572 H0 Z" fill="url(#panelGradient)"/>
      <path class="accent-curve" d="M548,0 C470,120 450,420 520,572 L536,572 C468,420 482,150 548,0 Z" fill="var(--accent-blue)"/>
    </svg>

    <div class="contact-side">
      <h1 class="person-name">Dale Brennick</h1>
      <p class="person-role">Owner</p>
      <div class="divider"></div>
      <address class="address">1234 First Line Address<br>5678 Second Line Address</address>
      <ul class="contact-list">
        <li>
          <svg viewBox="0 0 24 24" fill="none" stroke="var(--icon-grey)" stroke-width="2" stroke-linecap="round" stroke-linejoin="round"><path d="M5 3h4l2 5-3 2a11 11 0 0 0 6 6l2-3 5 2v4a2 2 0 0 1-2 2A17 17 0 0 1 3 5a2 2 0 0 1 2-2z"/></svg>
          555-014-2286
        </li>
        <li>
          <svg viewBox="0 0 24 24" fill="var(--icon-grey)"><path d="M2 5h20v14H2z"/><path d="M2 5l10 8 10-8" fill="none" stroke="var(--panel-dark-bottom)" stroke-width="1.6"/></svg>
          Dale@keystonetrenchco.example
        </li>
        <li>
          <svg viewBox="0 0 24 24" fill="none" stroke="var(--icon-grey)" stroke-width="1.8"><circle cx="12" cy="12" r="9"/><path d="M3 12h18M12 3c3 3 3 15 0 18M12 3c-3 3-3 15 0 18"/></svg>
          www.keystonetrenchco.example
        </li>
      </ul>
    </div>

    <div class="brand-mark">
      <span class="brand-dot"></span>
      <span class="brand-name">Keystone Trench Co</span>
    </div>
  </div>
</body>
</html>
```